Business Card Design

Hi I need a business card designed, we already have the business name logo artwork and would like some concept ideas for the Bus Card layout.
On the back of the card i want to include the products and services that we offer.
We are a Plastics Sheeting manufacture based in Perth Australia.

                                       

We need a BC design for a company called Tarvo Plastics based in Perth Australia.

We supply from DIY to Trade & Industrial  Engineering Markets.

We specialise in:

·         Cut to size panels  (all shapes and sizes)

·         Plastics fabrication & Welding

·         Custom Designs

·         Plastic Repairs

·         PVC Pipe Slotting & PVC Pipe Threading

·         Supplier of all types of engineering plastics and profiles.

Including:           Acrylic / Clarvene

                               Polycarbonate / Dorvil

                               Prismatic Light Diffuser

                               Vantrib

                               HDPE / UHMWPE

                               PVC / PVC Foam

                               Nylon

                               HIPS

```html
<!DOCTYPE html>
<html lang="en">
<head>
<meta charset="utf-8">
<title>Tarvo Plastics – Business Card</title>
<link rel="stylesheet" href="https://fonts.googleapis.com/css2?family=Open+Sans:wght@400;600;700&display=swap">
<style>
  :root {
    --navy: #1c2b5e;
    --gold: #f2a81d;
    --orange: #e8811c;
    --white: #ffffff;
    --ink: #3d4150;
    --muted: #5a5e6b;
    --rule: #c9ccd4;
    --backdrop: #e9e6e1;
  }
  * { box-sizing: border-box; margin: 0; padding: 0; }
  html, body { width: 1200px; height: 720px; overflow: hidden; }
  body {
    background: var(--backdrop);
    font-family: "Open Sans", Arial, sans-serif;
    display: flex;
    align-items: center;
    justify-content: center;
    gap: 40px;
  }
  .card {
    position: relative;
    width: 540px;
    height: 310px;
    overflow: hidden;
    box-shadow: 0 6px 18px rgba(0,0,0,.18);
  }

  /* Front */
  .card-front { background: var(--white); }
  .front-band { position: absolute; inset: 0; }
  .brand-mark {
    position: absolute;
    left: 34px;
    top: 118px;
    display: flex;
    align-items: center;
    gap: 10px;
    color: var(--navy);
    font-weight: 700;
    font-size: 36px;
    letter-spacing: -.5px;
  }
  .brand-mark .square { width: 18px; height: 18px; background: var(--navy); }
  .contact-divider {
    position: absolute; left: 312px; top: 28px;
    width: 1px; height: 170px; background: var(--rule);
  }
  .contact-list {
    position: absolute; left: 326px; top: 26px;
    list-style: none; color: var(--ink); font-size: 12.5px; line-height: 19px;
  }
  .contact-list li { display: flex; align-items: center; gap: 6px; }
  .contact-list svg { width: 12px; height: 12px; flex: none; }
  .contact-address {
    position: absolute; left: 326px; top: 108px;
    color: var(--ink); font-size: 12.5px; line-height: 18px; font-style: normal;
  }
  .trading-line {
    position: absolute; left: 30px; top: 246px;
    color: var(--muted); font-size: 11px;
  }
  .person {
    position: absolute; right: 24px; top: 256px;
    color: var(--white); font-size: 17px;
  }
  .person strong { font-weight: 700; }
  .person span { font-size: 13px; font-weight: 400; }

  /* Back */
  .card-back { background: var(--navy); color: var(--white); }
  .back-brand {
    position: absolute; top: 18px; left: 0; right: 0;
    display: flex; justify-content: center; align-items: center; gap: 10px;
    font-weight: 700; font-size: 34px; letter-spacing: -.5px;
  }
  .back-brand .square { width: 16px; height: 16px; background: var(--white); }
  .back-headline {
    position: absolute; top: 72px; left: 20px; right: 20px;
    text-align: center; font-weight: 700; font-size: 12.5px; line-height: 17px;
  }
  .column-title { color: var(--gold); font-weight: 700; font-size: 16px; line-height: 22px; margin-bottom: 2px; }
  .services { position: absolute; left: 28px; top: 114px; width: 300px; }
  .materials { position: absolute; left: 352px; top: 114px; width: 170px; }
  .bullet-list { list-style: none; font-size: 12.5px; line-height: 17px; }
  .bullet-list li { position: relative; padding-left: 12px; }
  .bullet-list li::before {
    content: ""; position: absolute; left: 0; top: 6px;
    width: 6px; height: 6px; border-radius: 50%; background: var(--gold);
  }
  .column-divider {
    position: absolute; left: 338px; top: 120px;
    width: 1px; height: 140px; background: rgba(255,255,255,.45);
  }
</style>
</head>
<body>

  <section class="card card-front" aria-label="Business card front">
    <svg class="front-band" viewBox="0 0 540 310" width="540" height="310" aria-hidden="true">
      <path d="M0,268 L318,268 C340,268 344,236 372,236 L540,236" fill="none" stroke="var(--gold)" stroke-width="4"/>
      <path d="M0,274 L320,274 C342,274 346,242 374,242 L540,242 L540,310 L0,310 Z" fill="var(--navy)"/>
    </svg>

    <div class="brand-mark"><span class="square"></span>Tarvo Plastics</div>

    <div class="contact-divider"></div>
    <ul class="contact-list">
      <li>
        <svg viewBox="0 0 12 12"><circle cx="6" cy="6" r="5" fill="none" stroke="var(--orange)" stroke-width="1.4"/><path d="M4,3.5 L5,5.5 L4.5,6 Q5.5,7.5 6.5,7.5 L7,7 L8.5,8" fill="none" stroke="var(--orange)" stroke-width="1.1"/></svg>
        08 9400 1234
      </li>
      <li>
        <svg viewBox="0 0 12 12"><rect x="3" y="1" width="6" height="10" rx="1.2" fill="none" stroke="var(--orange)" stroke-width="1.3"/><circle cx="6" cy="9" r=".8" fill="var(--orange)"/></svg>
        0400 555 012
      </li>
      <li>
        <svg viewBox="0 0 12 12"><rect x="1" y="5" width="10" height="6" rx="1" fill="var(--orange)"/><rect x="3" y="1" width="6" height="4" fill="none" stroke="var(--orange)" stroke-width="1.2"/></svg>
        08 9400 1235
      </li>
      <li>
        <svg viewBox="0 0 12 12"><rect x="1" y="2.5" width="10" height="7" rx="1" fill="var(--orange)"/><path d="M1.5,3 L6,6.5 L10.5,3" fill="none" stroke="var(--white)" stroke-width="1"/></svg>
        sales@tarvoplastics.com.au
      </li>
    </ul>
    <address class="contact-address">
      Unit 4/18 Harlow Circuit<br>
      Brenfield WA 6112<br>
      PO Box 2240 Brenfield<br>
      DC WA 6992
    </address>

    <p class="trading-line">Kellan Group Pty Ltd T/A Tarvo Plastics ABN: TBA</p>
    <p class="person"><strong>Your Name,</strong> <span>Title</span></p>
  </section>

  <section class="card card-back" aria-label="Business card back">
    <div class="back-brand"><span class="square"></span>Tarvo Plastics</div>
    <p class="back-headline">The Products And Services That We Offer<br>Are Supplied From DIY To Trade &amp; Industrial Engineering Markets</p>

    <div class="services">
      <h2 class="column-title">We specialise in:</h2>
      <ul class="bullet-list">
        <li>Cut to size panels (all shapes and sizes)</li>
        <li>Plastics fabrication &amp; Welding</li>
        <li>Custom Designs</li>
        <li>Plastic Repairs</li>
        <li>PVC Pipe Slotting &amp; PVC Pipe Threading</li>
        <li>Supplier of all types of engineering plastics and profiles</li>
      </ul>
    </div>

    <div class="column-divider"></div>

    <div class="materials">
      <h2 class="column-title">Including:</h2>
      <ul class="bullet-list">
        <li>Acrylic / Clarvene</li>
        <li>Polycarbonate / Dorvil</li>
        <li>Prismatic Light Diffuser</li>
        <li>Vantrib</li>
        <li>HDPE / UHMWPE</li>
        <li>PVC / PVC Foam</li>
        <li>Nylon</li>
        <li>HIPS</li>
      </ul>
    </div>
  </section>

</body>
</html>
```